Home show booth design

We are looking at a home show booth design for our window and door company. We will have some high end doors, windows, patio door and garage door on display. 1 booth is 10x20 and 1 booth is 20x20.

Give me some design ideas and keeping in mind our product on display.

Below is our logo and i would like to keep our branding colors and i want a very attractive and high end setup to stand out from the crowd

Target Market(s)

Home owners and custom home builders

Industry/Entity Type

Windows and doors

Font styles to use
Serif

Colors

Designer to choose colors to be used in the design.

Requirements
Must have
• Back drop, small desk
Nice to have
• Large floating balloon above the booth

```html
<!DOCTYPE html>
<html lang="en">
<head>
<meta charset="utf-8">
<title>Keystone Doors &amp; Windows – Home Show Booth</title>
<link href="https://fonts.googleapis.com/css2?family=Poppins:wght@400;500;600;700&family=Roboto:wght@900&display=swap" rel="stylesheet">
<style>
  :root {
    --orange: #e06a1b;
    --orange-deep: #a63a08;
    --ink: #3b3830;
    --black: #1b1b1b;
    --charcoal: #2e2a24;
    --paper: #ffffff;
    --stage: #d4d4d4;
    --counter-top: #8a8a8a;
  }
  * { box-sizing: border-box; margin: 0; padding: 0; }
  html, body { width: 1200px; height: 840px; overflow: hidden; }
  body { background: var(--stage); font-family: "Poppins", sans-serif; position: relative; }

  /* Counter */
  .counter { position: absolute; left: 50px; top: 300px; width: 280px; }
  .counter__cap { height: 14px; background: var(--counter-top); border-radius: 4px; margin: 0 -8px; }
  .counter__band { height: 34px; background: var(--black); }
  .counter__panel { height: 290px; background: var(--paper); display: flex; flex-direction: column; align-items: center; justify-content: center; gap: 18px; }
  .counter__mark { width: 54px; height: 54px; background: var(--orange); }
  .counter__name { font-weight: 600; font-size: 22px; line-height: 1.2; color: var(--ink); text-align: center; }
  .counter__rule { height: 6px; background: var(--orange); }
  .counter__footer { height: 70px; background: var(--charcoal); display: flex; align-items: center; justify-content: center; color: var(--paper); font-weight: 600; font-size: 15px; }
  .counter__base { height: 56px; background: var(--black); border-radius: 0 0 8px 8px; }

  /* Backdrop */
  .backdrop { position: absolute; left: 380px; top: 50px; width: 770px; height: 740px; background: var(--paper); overflow: hidden; }
  .brand { position: absolute; top: 40px; left: 0; right: 0; display: flex; align-items: center; justify-content: center; gap: 18px; }
  .brand__mark { width: 72px; height: 72px; background: var(--orange); }
  .brand__name { font-weight: 600; font-size: 36px; color: var(--ink); }

  .headline { position: absolute; top: 150px; left: 0; right: 0; text-align: center; font-family: "Roboto", sans-serif; font-weight: 900; line-height: 1.08; }
  .headline__lead { display: block; color: var(--orange); font-size: 44px; }
  .headline__main { display: block; color: var(--ink); font-size: 48px; }

  .services-tab { position: absolute; top: 300px; left: 0; width: 270px; height: 44px; background: var(--orange); clip-path: polygon(0 0, 90% 0, 100% 100%, 0 100%); color: var(--paper); font-size: 26px; line-height: 44px; padding-left: 28px; }
  .services-tab strong { font-weight: 700; }
  .services { position: absolute; top: 362px; left: 28px; list-style: none; }
  .services li { font-size: 22px; color: var(--ink); line-height: 38px; }
  .services li::before { content: "•"; color: var(--orange); margin-right: 10px; }

  .contact { position: absolute; top: 530px; left: 28px; color: var(--black); }
  .contact__phone { font-size: 40px; font-weight: 700; line-height: 1.1; }
  .contact__web { font-size: 22px; font-weight: 600; }
  .contact__web span { color: var(--orange); }

  .band { position: absolute; left: 0; bottom: 0; width: 770px; height: 150px; }

  .gallery { position: absolute; top: 298px; left: 418px; width: 334px; padding: 6px; background: var(--paper); display: grid; grid-template-columns: 1fr 1fr; gap: 8px; }
  .gallery__photo { height: 196px; }
  .photo--entry { background: linear-gradient(160deg, #6b4a3a, #8a7a6a 55%, #5a5a62); }
  .photo--family { background: linear-gradient(160deg, #3d3a34, #b8a090 55%, #e8e4de); }
  .photo--bedroom { background: linear-gradient(160deg, #f2f2f2, #c8ccc8 55%, #8e7a68); }
  .photo--garage { background: linear-gradient(180deg, #6f98c8, #d8dde4 45%, #4a4a52); }
</style>
</head>
<body>

  <aside class="counter">
    <div class="counter__cap"></div>
    <div class="counter__band"></div>
    <div class="counter__panel">
      <div class="counter__mark"></div>
      <div class="counter__name">Keystone<br>Doors &amp; Windows</div>
    </div>
    <div class="counter__rule"></div>
    <div class="counter__footer">keystonedoorsco.com</div>
    <div class="counter__base"></div>
  </aside>

  <main class="backdrop">
    <div class="brand">
      <div class="brand__mark"></div>
      <div class="brand__name">Keystone Doors &amp; Windows</div>
    </div>

    <h1 class="headline">
      <span class="headline__lead">Elevate Your Home With</span>
      <span class="headline__main">Keystone Doors &amp; Windows</span>
    </h1>

    <div class="services-tab">Our <strong>Services</strong></div>
    <ul class="services">
      <li>High end Doors</li>
      <li>Windows</li>
      <li>Patio Door and</li>
      <li>Garage Door</li>
    </ul>

    <div class="contact">
      <div class="contact__phone">555.014.2280</div>
      <div class="contact__web">keystonedoorsco<span>.com</span></div>
    </div>

    <svg class="band" viewBox="0 0 770 150" preserveAspectRatio="none" aria-hidden="true">
      <defs>
        <linearGradient id="bandFill" x1="0" y1="0" x2="1" y2="0">
          <stop offset="0" stop-color="#8a2606"/>
          <stop offset="0.45" stop-color="#d05a12"/>
          <stop offset="1" stop-color="#e8751f"/>
        </linearGradient>
      </defs>
      <path d="M0 40 Q380 50 770 60 L770 150 L0 150 Z" fill="url(#bandFill)"/>
    </svg>

    <section class="gallery">
      <div class="gallery__photo photo--entry" role="img" aria-label="Craftsman-style home entrance with a wooden front door"></div>
      <div class="gallery__photo photo--family" role="img" aria-label="Family smiling behind a large window"></div>
      <div class="gallery__photo photo--bedroom" role="img" aria-label="Bright bedroom with large windows"></div>
      <div class="gallery__photo photo--garage" role="img" aria-label="House exterior with dark garage doors under a blue sky"></div>
    </section>
  </main>

</body>
</html>
```